Business Card Design for a Software Startup

We'd like to have a business card design. We already have a logo. Basically what we need is a clean design with name, address, cellphone and phone numbers, e-mail and web site address (front) and a space on the back with our logo with the company name on the right side and some texts on the bottom.
We are a development and consulting company in Brazil with highly qualified team of professionals in Java, iOS and Android development and consulting.

Target Market(s)

CIO, IT managers of mid to big size companies

Industry/Entity Type

Business

```html
<!DOCTYPE html>
<html lang="en">
<head>
<meta charset="utf-8">
<title>NORVEX Business Cards</title>
<link rel="stylesheet" href="https://fonts.googleapis.com/css2?family=Source+Sans+3:wght@400;600;700;800&display=swap">
<style>
  :root {
    --page-bg: #e6e7e9;
    --card-bg: #ffffff;
    --navy: #12306b;
    --brand-blue: #1f5fae;
    --sky-blue: #1d8fd8;
    --text-grey: #4a4f57;
    --divider: #d9dce1;
  }
  * { box-sizing: border-box; margin: 0; padding: 0; }
  html, body {
    width: 1200px;
    height: 720px;
    overflow: hidden;
    background: var(--page-bg);
    font-family: "Source Sans 3", "Helvetica Neue", Arial, sans-serif;
  }
  .canvas {
    position: relative;
    width: 1200px;
    height: 720px;
  }
  .card {
    position: absolute;
    top: 200px;
    width: 560px;
    height: 320px;
    background: var(--card-bg);
    box-shadow: 0 6px 18px rgba(0, 0, 0, 0.14);
    overflow: hidden;
  }
  .card--front { left: 25px; }
  .card--back { left: 615px; }

  .brand {
    display: flex;
    align-items: center;
    gap: 12px;
    color: var(--navy);
    font-weight: 800;
    letter-spacing: 1px;
  }
  .brand__square {
    width: 0.8em;
    height: 0.8em;
    background: var(--brand-blue);
    border-radius: 3px;
    flex: none;
  }

  /* Front */
  .card--front .brand {
    position: absolute;
    left: 36px;
    top: 88px;
    font-size: 40px;
  }
  .card__divider {
    position: absolute;
    left: 262px;
    top: 26px;
    width: 1px;
    height: 160px;
    background: var(--divider);
  }
  .contact {
    position: absolute;
    left: 288px;
    top: 22px;
    color: var(--text-grey);
  }
  .contact__name {
    font-size: 22px;
    font-weight: 700;
    color: var(--brand-blue);
    line-height: 1.05;
  }
  .contact__title {
    font-size: 14px;
    margin-bottom: 8px;
  }
  .contact__list { list-style: none; }
  .contact__item {
    display: flex;
    align-items: center;
    gap: 7px;
    font-size: 13.5px;
    line-height: 18px;
  }
  .contact__icon {
    width: 11px;
    height: 11px;
    flex: none;
  }
  .contact__address {
    margin-top: 10px;
    font-size: 13.5px;
    line-height: 17px;
  }
  .card__wave {
    position: absolute;
    left: 0;
    top: 0;
    width: 560px;
    height: 320px;
  }

  /* Back */
  .card--back .brand {
    position: absolute;
    left: 0;
    right: 0;
    top: 108px;
    justify-content: center;
    font-size: 50px;
  }
  .card__web {
    position: absolute;
    left: 0;
    right: 0;
    top: 228px;
    text-align: center;
    font-size: 18px;
    letter-spacing: 4px;
    color: var(--text-grey);
  }
</style>
</head>
<body>
<main class="canvas">

  <section class="card card--front" aria-label="Business card front">
    <svg class="card__wave" viewBox="0 0 560 320" aria-hidden="true">
      <defs>
        <linearGradient id="band-gradient" x1="0" y1="0" x2="1" y2="0">
          <stop offset="0" stop-color="var(--sky-blue)"/>
          <stop offset="1" stop-color="var(--brand-blue)"/>
        </linearGradient>
      </defs>
      <path d="M0,266 C180,244 370,226 560,214 L560,228 C370,240 180,262 0,286 Z" fill="var(--navy)"/>
      <path d="M0,300 C180,276 370,252 560,240 L560,320 L0,320 Z" fill="url(#band-gradient)"/>
    </svg>

    <div class="brand"><span class="brand__square"></span>NORVEX</div>
    <div class="card__divider"></div>

    <div class="contact">
      <p class="contact__name">Your Name</p>
      <p class="contact__title">Title</p>
      <ul class="contact__list">
        <li class="contact__item">
          <svg class="contact__icon" viewBox="0 0 12 12" aria-hidden="true"><circle cx="6" cy="6" r="6" fill="var(--text-grey)"/><path d="M3.6 3.2 L5 3 L5.5 4.6 L4.7 5.2 Q5.4 6.7 6.8 7.3 L7.4 6.5 L9 7 L8.8 8.4 Q5.5 8.6 3.6 3.2 Z" fill="#fff"/></svg>
          555-014-2870
        </li>
        <li class="contact__item">
          <svg class="contact__icon" viewBox="0 0 12 12" aria-hidden="true"><circle cx="6" cy="6" r="6" fill="var(--text-grey)"/><rect x="4.2" y="2.6" width="3.6" height="6.8" rx="0.8" fill="#fff"/><rect x="4.8" y="3.4" width="2.4" height="4.2" fill="var(--text-grey)"/></svg>
          555-019-6342
        </li>
        <li class="contact__item">
          <svg class="contact__icon" viewBox="0 0 12 12" aria-hidden="true"><circle cx="6" cy="6" r="6" fill="var(--text-grey)"/><rect x="2.8" y="3.8" width="6.4" height="4.4" fill="#fff"/><path d="M2.8 3.8 L6 6.4 L9.2 3.8" fill="none" stroke="var(--text-grey)" stroke-width="0.7"/></svg>
          yourname@norvex.com
        </li>
        <li class="contact__item">
          <svg class="contact__icon" viewBox="0 0 12 12" aria-hidden="true"><circle cx="6" cy="6" r="6" fill="var(--text-grey)"/><circle cx="6" cy="6" r="3.4" fill="none" stroke="#fff" stroke-width="0.8"/><path d="M2.6 6 H9.4 M6 2.6 V9.4" stroke="#fff" stroke-width="0.7"/></svg>
          www.norvex.com
        </li>
      </ul>
      <p class="contact__address">Door No. Street Name<br>City Name, State, Zip Codeo</p>
    </div>
  </section>

  <section class="card card--back" aria-label="Business card back">
    <div class="brand"><span class="brand__square"></span>NORVEX</div>
    <p class="card__web">www.norvex.com</p>
  </section>

</main>
</body>
</html>
```